Stationery Set for Velmora Company

I need to create full stationery design for my company; Business Cards, Envelops, Letter Heads, Calendar.
In the letter head and Envelops... only contact information and website links.
Our company is a Service Management company with different domains of innovative services including Technology Service Management, Education Services, Outsourcing Management, Events Management.
I need a modern and innovative design specially for the business card. I some transparent designs and I like it, but don't limit your innovation to what I mentioned. Sky is limit for your innovation.

Target Market(s)

Middle East & Africa

Industry/Entity Type

Business Management

Colors
34a7d8
0355a3
85acd3
86cae7
cee9f5
cfdeed
e4daeb
f3f1f8
ecf7fb

Requirements
Must have
• Name, Title, Email, Mobile
Nice to have
• We have multiple locations in USA, KSA, EGY, so I need ideas about how to include all contact details maybe QR / Barcode or something else.
• Please see our locations and contact information: www.brightvelmora.example
Should not have
• Too much text

```html
<!DOCTYPE html>
<html lang="en">
<head>
<meta charset="utf-8">
<title>Velmora Company — Envelope</title>
<link rel="stylesheet" href="https://fonts.googleapis.com/css2?family=Quicksand:wght@500;700&display=swap">
<style>
  :root {
    --page: #ffffff;
    --pearl-dark: #c9c6c5;
    --pearl-mid: #d8d6d5;
    --pearl-light: #efeeed;
    --brand-grey: #8d8c8c;
    --address-blue: #34a7d8;
    --band: #f3f2f2;
    --window: #ffffff;
    --window-edge: #6f6f6f;
  }
  * { margin: 0; padding: 0; box-sizing: border-box; }
  html, body { width: 1200px; height: 1000px; overflow: hidden; background: var(--page); }
  .canvas { position: relative; width: 1200px; height: 1000px; }
  .envelope {
    position: absolute; left: 25px; top: 100px; width: 1143px; height: 806px;
    background: linear-gradient(90deg,
      var(--pearl-dark) 0%, var(--pearl-mid) 12%, var(--pearl-dark) 24%,
      var(--pearl-light) 40%, var(--pearl-mid) 52%, var(--pearl-light) 66%,
      var(--pearl-dark) 78%, var(--pearl-light) 90%, var(--pearl-mid) 100%);
    box-shadow: -4px 4px 8px rgba(0,0,0,0.35);
    overflow: hidden;
  }
  .wave-decor {
    position: absolute; left: 0; top: 80px; width: 540px; height: 320px;
    background: linear-gradient(160deg, rgba(255,255,255,0.45), rgba(200,198,197,0.15) 60%, rgba(255,255,255,0));
    border-top-right-radius: 100% 60%;
  }
  .brand-name {
    position: absolute; left: 85px; top: 140px;
    font-family: "Quicksand", sans-serif; font-weight: 700; font-size: 34px;
    color: var(--brand-grey); letter-spacing: 0.5px;
  }
  .brand-mark {
    position: absolute; left: 88px; top: 200px; width: 12px; height: 12px;
    border-radius: 50%; background: var(--brand-grey);
  }
  .return-address {
    position: absolute; left: 88px; top: 270px;
    font-family: "Quicksand", sans-serif; font-weight: 500; font-size: 20px;
    line-height: 32px; color: var(--address-blue); font-style: normal;
  }
  .band {
    position: absolute; left: 0; top: 683px; width: 100%; height: 45px;
    background: linear-gradient(90deg, #e4e3e3, var(--band) 40%, #ffffff 100%);
  }
  .address-window {
    position: absolute; left: 635px; top: 556px; width: 455px; height: 191px;
    background: var(--window); border: 1px solid var(--window-edge); border-radius: 14px;
  }
</style>
</head>
<body>
<div class="canvas">
  <div class="envelope">
    <div class="wave-decor" role="img" aria-label="Soft grey flowing line pattern decoration"></div>
    <div class="brand-name">Velmora Company</div>
    <div class="brand-mark"></div>
    <address class="return-address">
      418 Harbor Crest Lane, 4th<br>
      Floor Lakemont CA 90210<br>
      US
    </address>
    <div class="band"></div>
    <div class="address-window"></div>
  </div>
</div>
</body>
</html>
```